New Innovative Counselling and psychotherapy Service needs Business Card design

Keep it simple and professional. On one side, just company name and logo (perhaps in all blue) and maybe a tag line.

On other side (all white) my name and Qualifications in centre

Industry/Entity Type

Health And Wellness

Contact Information for Business Card

Dara Whelby
Counsellor & Psychotherapist
BSc (Psychol.), BA, Dip. (Couns. & Psych.), PG.Cert (CBT), FGTrK, ONRE

I will also require Mobile no, Email and web site address of which I'll pass on to final designer.

Font styles to use
Sans Serif

Requirements
Must have
• My Logo Only and please use the colours in logo that is in it.
Should not have
• Any other images

```html
<!DOCTYPE html>
<html lang="en">
<head>
<meta charset="utf-8">
<title>Harbor Lane – Business Card</title>
<link rel="stylesheet" href="https://fonts.googleapis.com/css2?family=Montserrat:wght@400;700&family=Questrial&display=swap">
<style>
  :root {
    --backdrop: #2b2b2b;
    --card: #f7f8f8;
    --card-edge: #e6e8e9;
    --brand-blue: #3a9ad9;
    --ink-dark: #2d2f31;
    --ink-grey: #5b5f63;
    --mark-blue: #3a9ad9;
  }
  * { box-sizing: border-box; margin: 0; padding: 0; }
  html, body {
    width: 1200px;
    height: 997px;
    overflow: hidden;
    background: var(--backdrop);
  }
  .stage {
    position: relative;
    width: 1200px;
    height: 997px;
  }
  .card {
    position: absolute;
    width: 560px;
    height: 320px;
    background: var(--card);
    border: 1px solid var(--card-edge);
    border-radius: 18px;
    box-shadow: 0 14px 30px rgba(0, 0, 0, 0.45);
  }
  .card--back { left: 120px; top: 130px; }
  .card--front { left: 520px; top: 500px; }

  .profile {
    position: absolute;
    left: 48px;
    top: 110px;
    font-family: "Montserrat", sans-serif;
    color: var(--brand-blue);
  }
  .profile__name {
    font-size: 34px;
    letter-spacing: 1px;
    line-height: 1;
    text-transform: uppercase;
  }
  .profile__first { font-weight: 700; }
  .profile__last { font-weight: 400; }
  .profile__role {
    margin-top: 4px;
    font-size: 12.5px;
    color: var(--ink-grey);
    text-transform: uppercase;
    letter-spacing: 0.6px;
  }
  .profile__qualifications {
    margin-top: 22px;
    font-size: 13.5px;
    line-height: 1.45;
    text-transform: uppercase;
    letter-spacing: 0.5px;
  }

  .brand {
    position: absolute;
    left: 180px;
    top: 128px;
    display: flex;
    align-items: center;
    gap: 16px;
    font-family: "Questrial", sans-serif;
  }
  .brand__dot {
    width: 44px;
    height: 44px;
    border-radius: 50%;
    background: var(--mark-blue);
    flex: none;
  }
  .brand__name {
    font-size: 30px;
    line-height: 1;
    color: var(--ink-dark);
  }
  .brand__tagline {
    margin-top: 5px;
    font-size: 20px;
    color: var(--brand-blue);
    letter-spacing: 0.5px;
  }
</style>
</head>
<body>
  <main class="stage">
    <section class="card card--back" aria-label="Card back">
      <div class="profile">
        <h1 class="profile__name"><span class="profile__first">Dara</span> <span class="profile__last">Whelby</span></h1>
        <p class="profile__role">Counsellor &amp; Psychotherapist</p>
        <p class="profile__qualifications">
          BSc (Psychol.),<br>
          BA, Dip. (Couns. &amp; Psych.),<br>
          PG.Cert (CBT), FGTrK, ONRE
        </p>
      </div>
    </section>

    <section class="card card--front" aria-label="Card front">
      <div class="brand">
        <span class="brand__dot" aria-hidden="true"></span>
        <div class="brand__text">
          <p class="brand__name">Harbor Lane</p>
          <p class="brand__tagline">Your Tagline here</p>
        </div>
      </div>
    </section>
  </main>
</body>
</html>
```